Marlowby Services Website Design

We have most content but require a professional design. We have a logo already and will need it utilized along with several of the photos from the attached documentation.
First page should have our mission and Vision and the synapsis provided in the word document. Visitors will be prompted to select from one of our 3 divisions from this page.
Each division will have the same list of tabs : About, Services, Safety, Careers and Contact.
Photos on each divisions page should be representative of the divisions offerings. The word doc attached contains the requested content and we are open to edits that would complement and fill the website.
I like the Quorvane site www.quorvane.example - they are our competition so cant be modeled directly after this.
Please include prompts to request quote at each service page. align the format of the geotechnical page to the other 2 divisions.
I used chat gpt for some of the content so will need it optimized for SCO.

```html
<!DOCTYPE html>
<html lang="en">
<head>
<meta charset="utf-8">
<title>Marlowby Services</title>
<link href="https://fonts.googleapis.com/css2?family=Montserrat:wght@400;500;600;700;800&display=swap" rel="stylesheet">
<style>
:root{
  --red:#e8202a;
  --red-dark:#c5141d;
  --ink:#1d1d1f;
  --text:#555;
  --dark:#3a3a3a;
  --pink:#fbe3e4;
  --white:#fff;
}
*{box-sizing:border-box;margin:0;padding:0}
html,body{width:1200px;height:3896px;overflow:hidden}
body{font-family:"Montserrat",sans-serif;color:var(--ink);background:var(--white);position:relative}
.btn{display:inline-block;background:var(--red);color:var(--white);font-weight:600;font-size:15px;border-radius:30px;padding:14px 40px;text-decoration:none}
.section-title{font-size:40px;font-weight:700;text-align:center;color:var(--ink)}
.title-rule{width:150px;height:4px;background:var(--red);margin:12px auto 0}

/* header */
.site-header{position:absolute;top:0;left:0;width:1200px;height:80px;background:var(--white);display:flex;align-items:center;padding:0 100px;z-index:3}
.brand{font-size:30px;font-weight:800;color:var(--red);letter-spacing:1px}
.nav{display:flex;gap:40px;margin-left:70px}
.nav a{font-size:14px;font-weight:600;color:var(--ink);text-decoration:none;text-transform:uppercase}
.site-header .btn{margin-left:auto}

/* hero */
.hero{position:absolute;top:80px;left:0;width:1200px;height:600px}
.hero-photo{position:absolute;inset:0;background:linear-gradient(110deg,#1e2226 0%,#3b4047 40%,#6b6f72 70%,#9aa0a3 100%)}
.hero-copy{position:absolute;left:110px;top:140px;color:var(--white);width:420px}
.hero-copy .kicker{font-size:30px;font-weight:700;letter-spacing:1px}
.hero-copy h1{font-size:58px;font-weight:800;line-height:1.05;letter-spacing:2px}
.hero-copy p{font-size:15px;line-height:1.5;margin:14px 0 26px}
.hero-copy .btn{padding:12px 34px;font-size:14px}
.hero-edge{position:absolute;left:0;bottom:-20px;width:1200px;height:120px}

/* services */
.services{position:absolute;top:720px;left:0;width:1200px}
.service-row{position:absolute;top:120px;left:90px;width:1020px;height:340px}
.arrow{position:absolute;top:150px;width:44px;height:44px;border-radius:50%;display:flex;align-items:center;justify-content:center;background:var(--white)}
.arrow.prev{left:-70px;border:2px solid #aaa}
.arrow.next{right:-70px;border:2px solid var(--red)}
.service-card{position:absolute;top:0;width:238px;height:340px;background:var(--white);box-shadow:0 4px 18px rgba(0,0,0,.15);padding:26px 20px 20px;text-align:center;display:flex;flex-direction:column;overflow:hidden}
.service-card.active{top:-10px;height:360px;border-bottom:4px solid var(--red)}
.service-card h3{font-size:19px;font-weight:600;margin:16px 0 10px;line-height:1.3}
.service-card p{font-size:13px;line-height:20px;color:var(--text);overflow:hidden}
.hex-icon{width:96px;height:96px;margin:0 auto;flex:none}

/* vision */
.vision{position:absolute;top:1280px;left:0;width:1200px;height:360px;background:var(--pink);text-align:center;padding-top:110px}
.vision p{font-size:15px;line-height:1.6;color:#444;width:820px;margin:38px auto 30px}

/* mission */
.mission{position:absolute;top:1720px;left:0;width:1200px;height:560px}
.mission-photo{position:absolute;left:165px;top:40px;width:360px;height:410px}
.mission-copy{position:absolute;left:600px;top:30px;width:470px}
.mission-copy .section-title{text-align:left}
.mission-copy .title-rule{margin:12px 0 28px}
.mission-copy p{font-size:15px;line-height:1.65;color:var(--text)}
.mission-copy .btn{margin-top:26px}

/* contact */
.contact{position:absolute;top:2300px;left:0;width:1200px;height:500px;background:var(--dark)}
.contact-info{position:absolute;left:115px;top:50px;color:var(--white)}
.contact-info h2{font-size:40px;font-weight:700;margin-bottom:32px}
.contact-info li{list-style:none;display:flex;align-items:flex-start;gap:16px;font-size:19px;font-weight:600;margin-bottom:26px;line-height:1.4}
.contact-info svg{flex:none;margin-top:2px}
.contact-form{position:absolute;left:660px;top:10px;width:372px;height:390px;background:var(--white);padding:24px 26px;box-shadow:0 6px 20px rgba(0,0,0,.3)}
.contact-form h3{font-size:20px;font-weight:600;margin-bottom:14px}
.field{border-bottom:1px solid #bbb;font-size:13px;color:#666;padding:10px 0 12px}
.field.message{height:100px}
.contact-form .btn{position:absolute;right:26px;bottom:24px;padding:12px 36px}
.contact-edge{position:absolute;left:0;bottom:-1px;width:1200px;height:70px}

/* divisions */
.divisions{position:absolute;top:2840px;left:0;width:1200px}
.division-card{position:absolute;top:80px;width:300px;height:470px;background:var(--white);box-shadow:0 4px 18px rgba(0,0,0,.15);padding:14px 14px 24px;text-align:center;display:flex;flex-direction:column;align-items:center}
.division-photo{width:272px;height:224px;flex:none}
.division-card h3{font-size:21px;font-weight:600;line-height:1.3;height:56px;margin:18px 0 8px;display:flex;align-items:center;justify-content:center}
.division-card p{font-size:14px;line-height:1.55;color:var(--text);padding:0 10px}
.division-card .btn{margin-top:auto;padding:12px 38px}

/* footer */
.site-footer{position:absolute;top:3440px;left:0;width:1200px;height:456px;background:var(--red);color:var(--white)}
.footer-edge{position:absolute;top:-1px;left:0;width:1200px;height:110px}
.footer-brand{position:absolute;left:110px;top:200px;font-size:34px;font-weight:800;letter-spacing:1px}
.social{position:absolute;left:150px;top:262px;display:flex;gap:26px}
.social span{width:30px;height:30px;border:2px solid var(--white);border-radius:50%}
.footer-col{position:absolute;top:170px}
.footer-col h4{font-size:24px;font-weight:700;margin-bottom:12px}
.footer-col li{list-style:none;font-size:14px;line-height:1.75}
.footer-contact li{display:flex;gap:10px;align-items:flex-start}
.footer-contact svg{flex:none;margin-top:5px}
.copyright{position:absolute;left:0;bottom:0;width:1200px;height:44px;border-top:1px solid rgba(255,255,255,.35);font-size:13px;display:flex;align-items:center;justify-content:center}
</style>
</head>
<body>

<header class="site-header">
  <div class="brand">MARLOWBY</div>
  <nav class="nav">
    <a href="#">About</a><a href="#">Services</a><a href="#">Safety</a><a href="#">Careers</a><a href="#">Contact</a>
  </nav>
  <a class="btn" href="#">Contact Us</a>
</header>

<section class="hero">
  <div class="hero-photo" role="img" aria-label="Aerial boom truck on a worksite road"></div>
  <div class="hero-copy">
    <div class="kicker">WELCOME TO</div>
    <h1>MARLOWBY</h1>
    <p>Marlowby is a full-service wind energy service provider specializing in blade access and repair, service and</p>
    <a class="btn" href="#">Get Started</a>
  </div>
  <svg class="hero-edge" viewBox="0 0 1200 120" preserveAspectRatio="none">
    <polygon points="0,40 600,95 1200,10 1200,40 600,120 0,70" fill="#e8202a"/>
    <polygon points="0,70 600,120 1200,40 1200,120 0,120" fill="#fff"/>
  </svg>
</section>

<section class="services">
  <h2 class="section-title">Our Services</h2>
  <div class="title-rule"></div>
  <div class="service-row">
    <div class="arrow prev"><svg width="16" height="16" viewBox="0 0 16 16"><path d="M10 2 L4 8 L10 14" stroke="#888" stroke-width="2.5" fill="none"/></svg></div>
    <div class="service-card">
      <svg class="hex-icon" viewBox="0 0 100 100"><polygon points="50,4 90,27 90,73 50,96 10,73 10,27" fill="#e8202a"/><rect x="28" y="40" width="30" height="20" fill="#fff"/><path d="M58 46 h10 l6 8 v6 h-16z" fill="#fff"/><circle cx="36" cy="64" r="5" fill="#fff"/><circle cx="66" cy="64" r="5" fill="#fff"/></svg>
      <h3>Delivering safe</h3>
      <p>Lorem Ipsum is simply dummy text of the printing and typesetting industry. Lorem Ipsum has been the industry's standard dummy text ever.</p>
    </div>
    <div class="service-card" style="left:260px">
      <svg class="hex-icon" viewBox="0 0 100 100"><polygon points="50,4 90,27 90,73 50,96 10,73 10,27" fill="#e8202a"/><circle cx="50" cy="50" r="22" fill="none" stroke="#fff" stroke-width="4"/><path d="M53 32 L40 53 h10 l-3 15 l13 -21 h-10z" fill="#fff"/></svg>
      <h3>Renewable energy industries</h3>
      <p>Lorem Ipsum is simply dummy text of the printing and typesetting industry. Lorem Ipsum has been the industry's</p>
    </div>
    <div class="service-card active" style="left:520px">
      <svg class="hex-icon" viewBox="0 0 100 100"><polygon points="50,4 90,27 90,73 50,96 10,73 10,27" fill="#e8202a"/><circle cx="50" cy="50" r="16" fill="none" stroke="#fff" stroke-width="8" stroke-dasharray="6 4"/><circle cx="50" cy="50" r="9" fill="#fff"/><circle cx="50" cy="50" r="4" fill="#e8202a"/></svg>
      <h3>Reliable Aerial Access And Maintenance Services To Oil&amp;gas</h3>
      <p>Lorem Ipsum is simply dummy text of the printing and</p>
    </div>
    <div class="service-card" style="left:780px">
      <svg class="hex-icon" viewBox="0 0 100 100"><polygon points="50,4 90,27 90,73 50,96 10,73 10,27" fill="#e8202a"/><path d="M30 58 a20 20 0 0 1 40 0z" fill="#fff"/><rect x="26" y="58" width="48" height="6" fill="#fff"/><rect x="46" y="34" width="8" height="10" fill="#e8202a"/></svg>
      <h3>Construction</h3>
      <p>Lorem Ipsum is simply dummy text of the printing and typesetting industry. Lorem Ipsum has been the industry's standard dummy text ever</p>
    </div>
    <div class="arrow next"><svg width="16" height="16" viewBox="0 0 16 16"><path d="M6 2 L12 8 L6 14" stroke="#e8202a" stroke-width="2.5" fill="none"/></svg></div>
  </div>
</section>

<section class="vision">
  <h2 class="section-title">Our Vision</h2>
  <div class="title-rule"></div>
  <p>To be the leading provider of aerial access, geotechnical drilling, and service solutions, setting the standard for excellence in safety, efficiency, and environmental stewardship.</p>
  <a class="btn" href="#">Contact Us</a>
</section>

<section class="mission">
  <svg class="mission-photo" viewBox="0 0 360 410" role="img" aria-label="Aerial lift truck beside a wind turbine tower">
    <defs><linearGradient id="sky" x1="0" y1="0" x2="0" y2="1"><stop offset="0" stop-color="#9cc3e6"/><stop offset=".6" stop-color="#cfe0ee"/><stop offset="1" stop-color="#8a8a7a"/></linearGradient></defs>
    <polygon points="180,4 352,104 352,306 180,406 8,306 8,104" fill="url(#sky)" stroke="#c5141d" stroke-width="6"/>
  </svg>
  <div class="mission-copy">
    <h2 class="section-title">Our Mission</h2>
    <div class="title-rule"></div>
    <p>At Marlowby, our mission is to deliver unparalleled aerial access, geotechnical drilling, and service and maintenance solutions, consistently exceeding our clients' expectations. We strive to achieve this by investing in cutting-edge technology, fostering a culture of safety and continuous improvement, and prioritizing environmental sustainability. Through collaboration, integrity, and dedication, we aim to contribute to the success of our clients while maintaining the highest standards of quality and professionalism.</p>
    <a class="btn" href="#">Read More</a>
  </div>
</section>

<section class="contact">
  <div class="contact-info">
    <h2>Contact Us</h2>
    <ul>
      <li><svg width="24" height="20" viewBox="0 0 24 20"><rect x="1" y="2" width="22" height="16" rx="2" fill="#fff"/><path d="M2 4 L12 11 L22 4" stroke="#3a3a3a" stroke-width="2" fill="none"/></svg>info@marlowbyservices.example</li>
      <li><svg width="24" height="24" viewBox="0 0 24 24"><path d="M5 2 h4 l2 5 -3 2 a12 12 0 0 0 7 7 l2 -3 5 2 v4 a2 2 0 0 1 -2 2 A18 18 0 0 1 3 4 a2 2 0 0 1 2 -2z" fill="#fff"/></svg>+1 555 010 8888</li>
      <li><svg width="24" height="26" viewBox="0 0 24 26"><path d="M12 1 a9 9 0 0 1 9 9 c0 7 -9 15 -9 15 s-9 -8 -9 -15 a9 9 0 0 1 9 -9z" fill="#fff"/><circle cx="12" cy="10" r="3.5" fill="#3a3a3a"/></svg>27 Ferrow Lane Calder Ridge AB<br>T0X-1B0</li>
    </ul>
  </div>
  <form class="contact-form">
    <h3>Drop Your Message</h3>
    <div class="field">Your Name</div>
    <div class="field">Your Email Address</div>
    <div class="field">Your Phone Number</div>
    <div class="field message">Message</div>
    <a class="btn" href="#">Submit</a>
  </form>
  <svg class="contact-edge" viewBox="0 0 1200 70" preserveAspectRatio="none">
    <polygon points="0,20 600,60 1200,0 1200,14 600,70 0,34" fill="#e8202a"/>
    <polygon points="0,34 600,70 1200,14 1200,70 0,70" fill="#fff"/>
  </svg>
</section>

<section class="divisions">
  <h2 class="section-title">Select Division</h2>
  <div class="title-rule"></div>
  <div class="division-card" style="left:115px">
    <div class="division-photo" role="img" aria-label="Aerial access lift working on a tower" style="background:linear-gradient(180deg,#7fb3de,#c4dced 70%,#8d8d86)"></div>
    <h3>Aerial Access</h3>
    <p>Lorem Ipsum is simply dummy text of the printing and typesetting industry. Lorem Ipsum has been the industry's standard dummy text ever since the</p>
    <a class="btn" href="#">Read More</a>
  </div>
  <div class="division-card" style="left:450px">
    <div class="division-photo" role="img" aria-label="Geotechnical drilling rig on a winter site" style="background:linear-gradient(180deg,#8fb0cf,#c8d3dc 60%,#7b6c5e)"></div>
    <h3>Geotechnical Drilling</h3>
    <p>Lorem Ipsum is simply dummy text of the printing and typesetting industry. Lorem Ipsum has been the industry's standard dummy text ever since the</p>
    <a class="btn" href="#">Read More</a>
  </div>
  <div class="division-card" style="left:785px">
    <div class="division-photo" role="img" aria-label="Wind turbine against a blue sky" style="background:linear-gradient(180deg,#3f86cf,#8ec0e8 70%,#d5e6f2)"></div>
    <h3>Renewable Energy<br>Services</h3>
    <p>Lorem Ipsum is simply dummy text of the printing and typesetting industry. Lorem Ipsum has been the industry's standard dummy text ever since the</p>
    <a class="btn" href="#">Read More</a>
  </div>
</section>

<footer class="site-footer">
  <svg class="footer-edge" viewBox="0 0 1200 110" preserveAspectRatio="none">
    <polygon points="0,0 1200,0 1200,30 600,95 0,30" fill="#fff"/>
    <polyline points="0,44 600,110 1200,44" stroke="#fff" stroke-width="3" fill="none"/>
  </svg>
  <div class="footer-brand">MARLOWBY</div>
  <div class="social"><span></span><span></span></div>
  <div class="footer-col" style="left:380px">
    <h4>Quick links</h4>
    <ul><li>About</li><li>Services</li><li>Safety</li><li>Careers</li><li>Contact</li></ul>
  </div>
  <div class="footer-col" style="left:610px">
    <h4>Other links</h4>
    <ul><li>Privacy Policy</li><li>Careers</li><li>Terms Condition</li></ul>
  </div>
  <div class="footer-col footer-contact" style="left:855px">
    <h4>Contact Info</h4>
    <ul>
      <li><svg width="14" height="14" viewBox="0 0 24 20"><rect x="1" y="2" width="22" height="16" rx="2" fill="#fff"/></svg>info@marlowbyservices.example</li>
      <li><svg width="14" height="14" viewBox="0 0 24 24"><path d="M5 2 h4 l2 5 -3 2 a12 12 0 0 0 7 7 l2 -3 5 2 v4 a2 2 0 0 1 -2 2 A18 18 0 0 1 3 4 a2 2 0 0 1 2 -2z" fill="#fff"/></svg>+1 555 010 8888</li>
      <li><svg width="14" height="16" viewBox="0 0 24 26"><path d="M12 1 a9 9 0 0 1 9 9 c0 7 -9 15 -9 15 s-9 -8 -9 -15 a9 9 0 0 1 9 -9z" fill="#fff"/></svg>27 Ferrow Lane Calder Ridge<br>AB T0X-1B0</li>
    </ul>
  </div>
  <div class="copyright">Copyright © 2024 Marlowby | All Rights Reserved</div>
</footer>

</body>
</html>
```